BRANDEMEIER & BRANDEMEIER,LLP NEEDS A NEW LETTERHEAD DESIGN

a conservative yet contemporary layout befitting a long established
firm, consistent with the times, some form of logo so it catches ones attention, and is
admirable, but portrays integrity
Updates

I would like to approve #22066987 Please advise how to do this as it’s confusing on the site so I can approve payment for the designer

Target Market(s)

real estate investors and building management people

Industry/Entity Type

Law Firm

Font styles to use
Serif

Colors

Designer to choose colors to be used in the design.

Requirements
Must have
• some form of conservative logo

```html
<!DOCTYPE html>
<html lang="en">
<head>
<meta charset="utf-8">
<title>Brandemeier &amp; Brandemeier, LLP — Letterhead</title>
<link rel="stylesheet" href="https://fonts.googleapis.com/css2?family=Arimo:wght@400;700&family=Cinzel:wght@500&display=swap">
<style>
  :root {
    --paper: #f3f3f3;
    --ink: #2a2a2a;
    --ink-soft: #444444;
    --brand: #3a3a3a;
    --brand-mark: #a9a9a9;
  }
  html, body {
    margin: 0;
    padding: 0;
    width: 1200px;
    height: 1166px;
    overflow: hidden;
    background: var(--paper);
  }
  .letterhead {
    position: relative;
    width: 1200px;
    height: 1166px;
    font-family: "Arimo", Arial, sans-serif;
    color: var(--ink);
  }
  .brand-mark {
    position: absolute;
    left: 283px;
    top: 122px;
  }
  .brand-name {
    position: absolute;
    left: 366px;
    top: 134px;
    margin: 0;
    font-family: "Cinzel", Georgia, serif;
    font-weight: 500;
    font-size: 17.5px;
    letter-spacing: 0.2px;
    color: var(--brand);
    white-space: nowrap;
  }
  .brand-tagline {
    position: absolute;
    left: 366px;
    top: 166px;
    margin: 0;
    font-family: "Cinzel", Georgia, serif;
    font-weight: 500;
    font-size: 9.5px;
    letter-spacing: 4.6px;
    color: var(--brand);
    white-space: nowrap;
  }
  .firm-contact {
    position: absolute;
    right: 268px;
    top: 133px;
    margin: 0;
    text-align: right;
    font-size: 10.4px;
    line-height: 15.6px;
    color: var(--ink-soft);
    font-style: normal;
  }
  .firm-contact .gap { height: 15px; }
  .firm-contact b { color: var(--ink); font-weight: 700; }
  .recipient {
    position: absolute;
    left: 284px;
    top: 314px;
    margin: 0;
    font-size: 11.2px;
    line-height: 13.6px;
    font-style: normal;
  }
  .letter-body {
    position: absolute;
    left: 284px;
    top: 431px;
    width: 648px;
    font-size: 11.1px;
    line-height: 13.6px;
  }
  .letter-body p {
    margin: 0 0 13.6px;
    text-align: justify;
  }
  .closing {
    position: absolute;
    left: 284px;
    top: 769px;
    margin: 0;
    font-size: 11.2px;
  }
  .signature {
    position: absolute;
    left: 284px;
    top: 796px;
    width: 132px;
    height: 54px;
    background: linear-gradient(90deg, #e4e4e4, #d9d9d9);
  }
  .signatory {
    position: absolute;
    left: 284px;
    top: 864px;
    margin: 0;
    font-size: 11.2px;
    line-height: 13.6px;
  }
</style>
</head>
<body>
<main class="letterhead">
  <header>
    <svg class="brand-mark" width="68" height="68" viewBox="0 0 68 68" aria-hidden="true">
      <circle cx="34" cy="34" r="32" fill="none" stroke="var(--brand-mark)" stroke-width="2"/>
    </svg>
    <h1 class="brand-name">BRANDEMEIER &amp; BRANDEMEIER, LLP</h1>
    <p class="brand-tagline">ATTORNEYS AND COUNSELORS AT LAW</p>

    <address class="firm-contact">
      48 Harlow Street Suite 210<br>
      Brooklyn, New York 11201
      <div class="gap"></div>
      <b>T:</b> (718) 555-0142 · <b>F:</b> (718)-555-0178<br>
      <b>E:</b> info@bblawfirm.com · <b>www.bblawfirm.com</b>
    </address>
  </header>

  <address class="recipient">
    Mr. Leonard Marcheval<br>
    President and CEO<br>
    Veritas Labs LLC.<br>
    1480 Hudson Avenue, Suite 3200<br>
    New York, NY 10025
  </address>

  <section class="letter-body">
    <p>Dear Mr. Marcheval:</p>
    <p>As Chairperson of the Corporate Conscience Campaign - Helping the Homeless in New York, I am writing this to thank you personally for your company's support in last month's fund-raising effort.</p>
    <p>As I indicated when we spoke on the phone two weeks ago, the campaign was considered a resounding success, raising a total of $1.65 million to-date, significantly exceeding our target of $1 million. Some donations are still trickling in, so we could end up close to a total of $2 million.</p>
    <p>Veritas Labs was an influential leader throughout the entire three-month campaign. In fact, we couldn't have succeeded without the generous support of your company, both financially, and through your organizational and administrative assistance. Your Team Leader, Elaine Porter was particularly impressive, going above and beyond what we could have expected of someone performing as a volunteer while continuing on with her day-to-day duties. Please convey my special thanks to Elaine.</p>
    <p>I would also ask you to convey my sincere thanks and congratulations to all of those other people in your company who contributed in any way to the Helping the Homeless Campaign. Please tell them that the sum of their contributions resulted in a major success that they should all be proud of taking part in.</p>
    <p>I believe that the 27 companies that participated in this effort have set a new standard for social responsibility in this community, and have set a powerful example that will inspire other companies and organizations to do the same.</p>
    <p>I look forward to seeing you at the Mayor's special thank you reception next month.</p>
  </section>

  <p class="closing">Yours sincerely,</p>
  <div class="signature" role="img" aria-label="Handwritten signature of the fundraising chair"></div>
  <p class="signatory">Gregory Hallworth<br>Fundraising Chair</p>
</main>
</body>
</html>
```